Thornbury Building Company - Card Design

I am looking to use the logo designs that you already did for me to develop a business card. I would like the card to have a black background and be double sided. I want white and green logo and text. I have attached an inspiration photo of a look that I like. I would like to use the Vertical Logo attached to take up the full front side of the card. On the back where I have my name and information, I would like to have the horizontal logo or maybe even just the image of the 'A' and trees without the text. I am open, but I am looking for something clean and simple and I want the green to really pop! Additional files can be found under Design #: 58302946

Target Market(s)

Homeowners

Industry/Entity Type

Construction

Contact Information for Business Card

Name: Marcus Thornbury, Title: Project Manager, Phone: 555.274.8136, Email: thornburybuildingcompany@mailvesta.com, address: 487 Larkspur Ln, Ridgeview, NV 95033, Lic# 2468317

Colors
00AB8E
00BBA5
67D7C9
C6EFE9
E9F9F6

Requirements
Nice to have
• I would like to see the logos that I have already got from ArtLoomHub, though I am open to new ones

```html
<!DOCTYPE html>
<html lang="en">
<head>
<meta charset="utf-8">
<title>Thornbury Building Company – Business Card</title>
<link rel="stylesheet" href="https://fonts.googleapis.com/css2?family=Open+Sans:wght@400;700&display=swap">
<style>
  :root {
    --backdrop: #4b4b4b;
    --card-black: #161616;
    --brand-green: #3cb54a;
    --text-green: #6cb544;
    --white: #ffffff;
  }
  * { margin: 0; padding: 0; box-sizing: border-box; }
  html, body { width: 1200px; height: 801px; overflow: hidden; }
  body {
    background: var(--backdrop);
    font-family: "Open Sans", Arial, sans-serif;
    display: flex;
    align-items: center;
    justify-content: center;
    gap: 48px;
  }
  .card {
    width: 525px;
    height: 300px;
    position: relative;
    box-shadow: 0 10px 30px rgba(0,0,0,.35);
  }
  /* Contact side */
  .card--contact {
    background: var(--card-black);
    border-bottom: 3px solid var(--brand-green);
    color: var(--white);
  }
  .brand-mark {
    position: absolute;
    top: 44px;
    right: 40px;
    display: flex;
    align-items: center;
    gap: 12px;
  }
  .brand-mark__dot {
    width: 18px; height: 18px;
    background: var(--brand-green);
  }
  .brand-mark__name {
    font-weight: 700;
    font-size: 20px;
    line-height: 1.15;
    color: var(--white);
    text-transform: uppercase;
    letter-spacing: .04em;
  }
  .person {
    position: absolute;
    left: 34px;
    top: 140px;
  }
  .person__name {
    color: var(--text-green);
    font-weight: 700;
    font-size: 24px;
    line-height: 1.1;
  }
  .person__title {
    font-size: 15px;
    margin-top: 3px;
  }
  .divider {
    position: absolute;
    left: 34px; right: 34px;
    top: 198px;
    height: 1.5px;
    background: var(--text-green);
  }
  .contact-list {
    position: absolute;
    left: 34px;
    top: 214px;
    list-style: none;
    font-size: 13px;
    line-height: 1.9;
  }
  .contact-list li { display: flex; align-items: center; gap: 8px; }
  .contact-list svg { width: 12px; height: 12px; fill: var(--text-green); flex: none; }
  .address {
    position: absolute;
    right: 34px;
    top: 214px;
    text-align: right;
    font-size: 13px;
    line-height: 1.9;
  }
  /* Brand side */
  .card--brand {
    background: var(--brand-green);
    display: flex;
    align-items: center;
    justify-content: center;
  }
  .seal {
    width: 220px; height: 220px;
    border: 5px solid var(--white);
    border-radius: 50%;
    display: flex;
    align-items: center;
    justify-content: center;
    text-align: center;
  }
  .seal__name {
    color: var(--white);
    font-weight: 700;
    font-size: 22px;
    line-height: 1.2;
    text-transform: uppercase;
    letter-spacing: .04em;
  }
</style>
</head>
<body>
  <section class="card card--contact">
    <div class="brand-mark">
      <span class="brand-mark__dot"></span>
      <span class="brand-mark__name">Thornbury<br>Building Company</span>
    </div>
    <div class="person">
      <p class="person__name">Marcus Thornbury</p>
      <p class="person__title">Project Manager</p>
    </div>
    <div class="divider"></div>
    <ul class="contact-list">
      <li>
        <svg viewBox="0 0 24 24" aria-hidden="true"><path d="M6.6 10.8a15.1 15.1 0 0 0 6.6 6.6l2.2-2.2a1 1 0 0 1 1-.25 11.4 11.4 0 0 0 3.6.57 1 1 0 0 1 1 1V20a1 1 0 0 1-1 1A17 17 0 0 1 3 4a1 1 0 0 1 1-1h3.5a1 1 0 0 1 1 1c0 1.250.2 2.45.57 3.57a1 1 0 0 1-.25 1z"/></svg>
        555.274.8136
      </li>
      <li>
        <svg viewBox="0 0 24 24" aria-hidden="true"><path d="M2 5h20v14H2zm2 2v.5l8 5 8-5V7l-8 5z"/></svg>
        thornburybuildingcompany@mailvesta.com
      </li>
    </ul>
    <div class="address">
      <p>487 Larkspur Ln, Ridgeview, NV 95033</p>
      <p>Lic # 2468317</p>
    </div>
  </section>

  <section class="card card--brand">
    <div class="seal">
      <span class="seal__name">Thornbury<br>Building<br>Company</span>
    </div>
  </section>
</body>
</html>
```